Business card design for Veltrami Engineering Tandem

We need a new business card design along with all the necessary to place an order. The company is Veltrami Engineering Tandem and we recently updated our logo.

```html
<!DOCTYPE html>
<html lang="en">
<head>
<meta charset="utf-8">
<title>Veltrami Engineering Tandem — Business Card</title>
<link href="https://fonts.googleapis.com/css2?family=Poppins:wght@400;500;600&display=swap" rel="stylesheet">
<style>
  :root {
    --stage: #1d1d1f;
    --card: #2a2a2c;
    --card-deep: #1f1f21;
    --ink-grey: #a9a9ab;
    --ink-light: #d4d4d6;
    --accent: #f2c21b;
    --steel-1: #3a3a3d;
    --steel-2: #8d8d90;
  }
  * { margin: 0; padding: 0; box-sizing: border-box; }
  html, body { width: 1200px; height: 689px; overflow: hidden; }
  body {
    background: var(--stage);
    font-family: "Poppins", sans-serif;
    position: relative;
  }
  .card {
    position: absolute;
    width: 540px;
    height: 309px;
    border-radius: 18px;
    background: var(--card);
    overflow: hidden;
    box-shadow: 0 18px 40px rgba(0,0,0,.45);
  }
  .card--back { left: 36px; top: 190px; }
  .card--front { left: 624px; top: 190px; }

  /* back side */
  .back-pattern {
    position: absolute; inset: 0;
    background: radial-gradient(circle at 30% 30%, #2f2f31, var(--card-deep));
  }
  .brand {
    position: absolute;
    display: flex; align-items: center; gap: 10px;
    font-weight: 600;
    color: var(--ink-grey);
    letter-spacing: .12em;
    text-transform: uppercase;
    white-space: nowrap;
  }
  .brand__mark { width: 14px; height: 14px; background: var(--accent); flex: none; }
  .card--back .brand { right: 40px; top: 140px; font-size: 15px; }

  /* front side */
  .front-decor {
    position: absolute; right: 0; top: 0;
    width: 200px; height: 100%;
    background: linear-gradient(135deg, var(--steel-1) 0%, var(--steel-2) 60%, var(--steel-1) 100%);
    clip-path: polygon(40% 0, 100% 0, 100% 100%, 10% 100%);
  }
  .card--front .brand { left: 34px; top: 50px; font-size: 18px; }
  .person { position: absolute; left: 50px; top: 120px; }
  .person__name {
    color: var(--accent); font-weight: 600; font-size: 22px;
    text-transform: uppercase; letter-spacing: .02em; line-height: 1.1;
  }
  .person__role {
    color: var(--ink-light); font-size: 13px; font-weight: 500;
    text-transform: uppercase; letter-spacing: .06em; margin-top: 2px;
  }
  .person__bar {
    position: absolute; left: 28px; top: 124px;
    width: 10px; height: 38px; background: var(--accent);
  }
  .contact { position: absolute; left: 50px; top: 186px; list-style: none; }
  .contact li {
    display: flex; align-items: center; gap: 8px;
    color: var(--ink-light); font-size: 13px; line-height: 20px;
  }
  .contact svg { width: 12px; height: 12px; flex: none; }
  .address {
    position: absolute; left: 50px; top: 252px;
    color: var(--ink-light); font-size: 13px; line-height: 18px;
  }
</style>
</head>
<body>
  <section class="card card--back" aria-label="Card back">
    <div class="back-pattern" role="img" aria-label="Embossed repeating brand-mark pattern in dark grey"></div>
    <div class="brand"><span class="brand__mark"></span>Veltrami Engineering Tandem</div>
  </section>

  <section class="card card--front" aria-label="Card front">
    <div class="front-decor" role="img" aria-label="Large metallic grey brand-mark decoration"></div>
    <div class="brand"><span class="brand__mark"></span>Veltrami Engineering Tandem</div>

    <span class="person__bar"></span>
    <div class="person">
      <p class="person__name">Dorian Vale</p>
      <p class="person__role">Managing Director</p>
    </div>

    <ul class="contact">
      <li>
        <svg viewBox="0 0 12 12"><path d="M2.5 1h2l1 2.5-1.3 1a6 6 0 0 0 3.3 3.3l1-1.3L11 7.5v2c0 .8-.7 1.5-1.5 1.5A8.5 8.5 0 0 1 1 2.5C1 1.7 1.7 1 2.5 1z" fill="var(--accent)"/></svg>
        044-555 010 274
      </li>
      <li>
        <svg viewBox="0 0 12 12"><rect x="1" y="2.5" width="10" height="7" fill="var(--accent)"/><path d="M1 2.5l5 4 5-4" stroke="var(--card)" fill="none"/></svg>
        hello@veltrami.com
      </li>
      <li>
        <svg viewBox="0 0 12 12"><circle cx="6" cy="6" r="5" fill="none" stroke="var(--accent)" stroke-width="1.2"/><path d="M1 6h10M6 1c-2.5 3-2.5 7 0 10M6 1c2.5 3 2.5 7 0 10" fill="none" stroke="var(--accent)"/></svg>
        www.veltrami.com
      </li>
    </ul>
    <p class="address">48, Kestrel Lane<br>Harbour City, 402118</p>
  </section>
</body>
</html>
```